Business Card Design

We are a commercial real estate brokerage in San Francisco, leasing office buildings downtown.
I would like a clean, elegant look. Simple but powerful .

Industry/Entity Type

Business

Contact Information for Business Card

Derek Holloway
lic# 07258143
415.555.0172
derek@velt-commercial.example
velt-commercial.example

```html
<!DOCTYPE html>
<html lang="en">
<head>
<meta charset="UTF-8">
<title>Velt Commercial – Business Card</title>
<link href="https://fonts.googleapis.com/css2?family=Jost:wght@500;600&family=Open+Sans:wght@400&display=swap" rel="stylesheet">
<style>
  :root {
    --backdrop: #e9e7e4;
    --card-dark: #0e0f12;
    --card-light: #f4f4f2;
    --brand-blue: #6d809e;
    --ink: #2a2c30;
    --ink-soft: #55585e;
  }
  * { margin: 0; padding: 0; box-sizing: border-box; }
  html, body {
    width: 1200px; height: 768px; overflow: hidden;
    background: var(--backdrop);
  }
  .stage {
    position: relative; width: 1200px; height: 768px;
    display: flex; align-items: center; justify-content: center; gap: 40px;
  }
  .card {
    position: relative; width: 540px; height: 309px; overflow: hidden;
    box-shadow: 0 6px 18px rgba(0,0,0,.18);
  }
  .card--front { background: var(--card-dark); }
  .card--back { background: var(--card-light); }

  /* Brand lockup */
  .brand {
    display: flex; align-items: center; gap: 16px;
    font-family: "Jost", sans-serif; font-weight: 500;
    color: var(--brand-blue); text-transform: uppercase;
  }
  .brand__square { width: 34px; height: 34px; background: var(--brand-blue); flex: none; }
  .brand__name { font-size: 38px; line-height: 1.02; letter-spacing: 2px; }
  .brand__line { display: block; white-space: nowrap; }

  .card--front .brand {
    position: absolute; left: 50%; top: 50%; transform: translate(-50%, -50%);
  }

  /* Back side */
  .person { position: absolute; left: 44px; top: 40px; }
  .person__name {
    font-family: "Jost", sans-serif; font-weight: 600;
    font-size: 19px; color: var(--ink);
  }
  .person__title {
    font-family: "Open Sans", sans-serif; font-size: 10px;
    color: var(--ink-soft); margin-top: 2px;
  }
  .contact {
    position: absolute; left: 44px; bottom: 40px;
    font-family: "Open Sans", sans-serif; font-size: 12.5px; color: var(--ink);
    list-style: none;
  }
  .contact li { display: flex; align-items: center; gap: 8px; height: 21px; }
  .contact svg { width: 12px; height: 12px; fill: var(--ink-soft); flex: none; }

  .card--back .brand {
    position: absolute; right: 34px; bottom: 30px;
    writing-mode: vertical-rl; transform: rotate(180deg);
    gap: 12px;
  }
  .card--back .brand__name { font-size: 26px; letter-spacing: 1.5px; }
  .card--back .brand__square { width: 24px; height: 24px; }
</style>
</head>
<body>
<main class="stage">
  <section class="card card--front" aria-label="Card front">
    <div class="brand">
      <span class="brand__square"></span>
      <span class="brand__name"><span class="brand__line">Velt</span><span class="brand__line">Commercial</span></span>
    </div>
  </section>

  <section class="card card--back" aria-label="Card back">
    <div class="person">
      <h1 class="person__name">Derek Holloway</h1>
      <p class="person__title">Managing Director</p>
    </div>

    <ul class="contact">
      <li>LIC# 07258143</li>
      <li>
        <svg viewBox="0 0 24 24" aria-hidden="true"><path d="M6.6 10.8a15 15 0 0 0 6.6 6.6l2.2-2.2c.3-.3.7-.4 1-.2 1.1.4 2.3.6 3.6.6.6 0 1 .4 1 1V20c0 .6-.4 1-1 1A17 17 0 0 1 3 4c0-.6.4-1 1-1h3.5c.6 0 1 .4 1 1 0 1.3.2 2.5.6 3.6.1.3 0 .7-.2 1z"/></svg>
        415.555.0172
      </li>
      <li>
        <svg viewBox="0 0 24 24" aria-hidden="true"><path d="M2 5h20v14H2zm2 2v.5l8 5 8-5V7zm0 2.8V17h16V9.8l-8 5z"/></svg>
        derek@velt-commercial.example
      </li>
      <li>
        <svg viewBox="0 0 24 24" aria-hidden="true"><path d="M12 2a10 10 0 1 0 0 20 10 10 0 0 0 0-20zm6.9 6h-2.9a15 15 0 0 0-1.4-3.6A8 8 0 0 1 18.9 8zM12 4c.8 1.2 1.5 2.5 1.9 4h-3.8c.4-1.5 1.1-2.8 1.9-4zM4.3 14a8 8 0 0 1 0-4h3.4a16 16 0 0 0 0 4zm.8 2h2.9c.3 1.3.8 2.5 1.4 3.6A8 8 0 0 1 5.1 16zM8 8H5.1a8 8 0 0 1 4.3-3.6C8.8 5.5 8.3 6.7 8 8zm4 12c-.8-1.2-1.5-2.5-1.9-4h3.8c-.4 1.5-1.1 2.8-1.9 4zm2.3-6H9.7a14 14 0 0 1 0-4h4.6a14 14 0 0 1 0 4zm.3 5.6c.6-1.1 1.1-2.3 1.4-3.6h2.9a8 8 0 0 1-4.3 3.6zM16.3 14a16 16 0 0 0 0-4h3.4a8 8 0 0 1 0 4z"/></svg>
        www.velt-commercial.example
      </li>
    </ul>

    <div class="brand">
      <span class="brand__square"></span>
      <span class="brand__name"><span class="brand__line">Velt</span><span class="brand__line">Commercial</span></span>
    </div>
  </section>
</main>
</body>
</html>
```